Business card for Eyelash extension salon in Larkmont Heights,California USA

We need new business card for our salon in Larkmont Heights. The salon name is 'Lashvera' . We would like to have...Business name: Lashvera Name of person: will provide later Address 4720 N.Alder Crest Ave Larkmont Heights , CA 90099 Phone: will provide later (Text only) Web: www.lashverastudio.example Snapgrid icon, Circlebook icon follow us for seasonal campaign and news @lashverastudiolounge Design should look elegant, high-end, clean, simple, cohesive with my brand. Please refer my brand board. Business name color will be metallic bronzy color. Im thinking grey background or white background. Thanks

Target Market(s)

25-35. Gender neutral. People who are in Entertainment business industry.
This is High-end Eyelash extension salon in Larkmont Heights

Industry/Entity Type

Beauty Salon

Contact Information for Business Card

Business name: Lashvera
Name of person: will provide later
Address 4720 N.Alder Crest Ave Larkmont Heights , CA 90099
Phone: will provide later (Text only)
Web: www.lashverastudio.example
Snapgrid icon, Circlebook icon
follow us for seasonal campaign and news @lashverastudiolounge

Requirements
Must have
• Beautiful, elegant, clean and simple look but very attractive and modern
Should not have
• We don't like too clutter, too busy designs.

```html
<!DOCTYPE html>
<html lang="en">
<head>
<meta charset="utf-8">
<title>Lashvera Business Card</title>
<link href="https://fonts.googleapis.com/css2?family=Montserrat:wght@300;400;500;700&display=swap" rel="stylesheet">
<style>
  :root {
    --page: #ececec;
    --card-white: #f9f9f8;
    --card-grey: #9c9c9c;
    --pattern-grey: #a6a6a6;
    --bronze: #8c6b50;
    --bronze-band: #8f6e52;
    --text-grey: #7b7b7b;
    --rule: #c9c9c9;
    --white: #ffffff;
  }
  * { margin: 0; padding: 0; box-sizing: border-box; }
  html, body { width: 1200px; height: 1153px; overflow: hidden; }
  body {
    background: var(--page);
    font-family: "Montserrat", sans-serif;
    position: relative;
  }
  .card {
    position: absolute;
    left: 240px;
    width: 720px;
    height: 411px;
    overflow: hidden;
    box-shadow: 0 6px 18px rgba(0,0,0,0.12);
  }
  /* Front */
  .card-front { top: 120px; background: var(--card-white); }
  .front-brand {
    position: absolute;
    left: 0; top: 0;
    width: 340px; height: 352px;
    display: flex; align-items: center; justify-content: center;
  }
  .brand-name {
    font-weight: 400;
    font-size: 50px;
    letter-spacing: 2px;
    color: var(--bronze);
  }
  .divider {
    position: absolute;
    left: 340px; top: 64px;
    width: 1px; height: 220px;
    background: var(--rule);
  }
  .contact {
    position: absolute;
    left: 378px; top: 84px;
    color: var(--text-grey);
    font-size: 17px;
    line-height: 1.45;
    white-space: nowrap;
  }
  .contact-name {
    font-weight: 700;
    font-size: 27px;
    color: var(--bronze);
    line-height: 1.1;
  }
  .contact-role { font-size: 17px; margin-bottom: 14px; }
  .contact-row { display: flex; align-items: center; gap: 10px; }
  .contact-row.plain { padding-left: 28px; }
  .contact-row svg { flex: none; }
  .band {
    position: absolute;
    left: 0; bottom: 0;
    width: 100%; height: 59px;
    background: var(--bronze-band);
  }
  /* Back */
  .card-back { top: 612px; }
  .back-ground {
    position: absolute; inset: 0;
    background: radial-gradient(ellipse at center, var(--pattern-grey), var(--card-grey));
  }
  .back-brand {
    position: absolute;
    left: 0; top: 0; width: 100%; height: 300px;
    display: flex; align-items: center; justify-content: center;
  }
  .back-brand .brand-name { color: var(--white); font-size: 76px; font-weight: 300; letter-spacing: 4px; }
  .follow {
    position: absolute;
    left: 24px; right: 24px; bottom: 44px;
    display: flex; align-items: center; gap: 10px;
    color: var(--white);
    font-size: 12.5px;
    font-weight: 700;
    white-space: nowrap;
  }
  .social { display: flex; align-items: center; gap: 5px; font-weight: 500; font-size: 11px; }
  .social-dot {
    width: 15px; height: 15px; border-radius: 50%;
    border: 1.5px solid var(--white);
  }
</style>
</head>
<body>
  <section class="card card-front">
    <div class="front-brand"><span class="brand-name">Lashvera</span></div>
    <div class="divider"></div>
    <div class="contact">
      <p class="contact-name">Maren Solis</p>
      <p class="contact-role">Fashion Marketing</p>
      <p class="contact-row plain">4720 N.Alder Crest Ave</p>
      <p class="contact-row plain">Larkmont Heights , CA 90099</p>
      <p class="contact-row">
        <svg width="18" height="18" viewBox="0 0 18 18"><circle cx="9" cy="9" r="8" fill="none" stroke="#8c6b50" stroke-width="1.3"/><path d="M6.2 5.2c.4-.4.9-.4 1.2 0l.8 1.1c.2.3.2.7-.1 1l-.5.5c.4.9 1.1 1.6 2 2l.5-.5c.3-.3.7-.3 1-.1l1.1.8c.4.3.4.8 0 1.2l-.6.6c-2.6.3-6.1-3.2-5.8-5.8z" fill="#8c6b50"/></svg>
        1555 010 0199
      </p>
      <p class="contact-row">
        <svg width="18" height="18" viewBox="0 0 18 18"><circle cx="9" cy="9" r="8" fill="none" stroke="#8c6b50" stroke-width="1.3"/><circle cx="9" cy="9" r="4.2" fill="none" stroke="#8c6b50" stroke-width="1"/><path d="M4.8 9h8.4M9 4.8c-1.6 2.4-1.6 6 0 8.4M9 4.8c1.6 2.4 1.6 6 0 8.4" fill="none" stroke="#8c6b50" stroke-width="0.8"/></svg>
        www.lashverastudio.example
      </p>
    </div>
    <div class="band" role="img" aria-label="Bronze band with a fine wavy line pattern"></div>
  </section>

  <section class="card card-back">
    <div class="back-ground" role="img" aria-label="Grey background with a subtle wavy line pattern"></div>
    <div class="back-brand"><span class="brand-name">Lashvera</span></div>
    <div class="follow">
      <span class="social"><span class="social-dot"></span>Circlebook</span>
      <span class="social"><span class="social-dot"></span>Snapgrid</span>
      <span>Follow Us For Seasonal Campaign News @lashverastudiolounge</span>
    </div>
  </section>
</body>
</html>
```